A-Stand Directional Sign Design

Objective:
We need a professional graphic design for an A-Stand sign that will guide customers arriving in our parking lot to our office. The design should be visually clear, welcoming, and aligned with our brand identity.
REQUIREMENTS:
Two versions of the design:
- One with an arrow pointing left
- One with an arrow pointing right
(This allows us to place the A-Stand anywhere and flip the graphic as needed.)
DIMENSIONS:
- Viewable Area: 30" x 40"
BRAND ALIGNMENT:
- Colors, fonts, and overall style should match our website: www.glidemarrow.com
- Clean, modern, and professional look consistent with our aviation/tourism brand
CONTENT:
- Clear directional arrow (left or right depending on version)
- Text: “Office Entrance” or similar concise wording (designers may propose alternatives if they improve clarity)
READABILITY:
- Bold, high-contrast design for visibility from a distance
- Simple layout that avoids clutter
DELIVERABLES:
- Final artwork in print-ready format (PDF preferred)
- Two versions: Arrow Left and Arrow Right
DESIGN GOAL:
Ensure customers can easily find our office upon arrival, while reinforcing glideMARROW’s professional and welcoming brand image.
Target Market(s)
Tourism
Look and feel

```html
<!DOCTYPE html>
<html lang="en">
<head>
<meta charset="utf-8">
<title>glideMARROW – Office Entrance A-Stand Sign</title>
<link href="https://fonts.googleapis.com/css2?family=Poppins:wght@500;600&display=swap" rel="stylesheet">
<style>
  :root {
    --backdrop: #737373;
    --sign-bg: #f2f2f2;
    --brand-blue: #1f78bd;
    --ink: #2b2b2b;
    --photo-sky: #4cc3d4;
    --photo-sea: #3a8fa3;
    --photo-deep: #1d3a44;
  }
  * { margin: 0; padding: 0; box-sizing: border-box; }
  html, body {
    width: 1200px;
    height: 1200px;
    overflow: hidden;
    background: var(--backdrop);
    font-family: "Poppins", sans-serif;
  }
  .sign {
    position: absolute;
    left: 20px;
    top: 164px;
    width: 1160px;
    height: 871px;
    background: var(--sign-bg);
    overflow: hidden;
  }
  .sign__photo {
    position: absolute;
    left: 0;
    top: 117px;
    width: 464px;
    height: 637px;
    background: linear-gradient(180deg, var(--photo-sky) 0%, #a9dbe3 38%, var(--photo-sea) 62%, var(--photo-deep) 100%);
  }
  .sign__brand {
    position: absolute;
    right: 55px;
    top: 112px;
    font-weight: 600;
    font-size: 40px;
    line-height: 1;
    color: var(--brand-blue);
    letter-spacing: 0.5px;
  }
  .sign__title {
    position: absolute;
    left: 579px;
    top: 317px;
    font-weight: 500;
    font-size: 185px;
    line-height: 1;
    color: var(--brand-blue);
  }
  .sign__subtitle {
    position: absolute;
    left: 579px;
    top: 502px;
    font-weight: 500;
    font-size: 71px;
    line-height: 1;
    color: var(--ink);
  }
  .sign__arrow {
    position: absolute;
    left: 808px;
    top: 714px;
    width: 297px;
    height: 105px;
  }
</style>
</head>
<body>
  <main class="sign">
    <div class="sign__photo" role="img" aria-label="Passenger wearing a headset looking out of a helicopter cockpit over a coastline and blue sea"></div>

    <div class="sign__brand">glideMARROW</div>

    <h1 class="sign__title">Office</h1>
    <p class="sign__subtitle">Entrance</p>

    <svg class="sign__arrow" viewBox="0 0 297 105" aria-label="Arrow pointing right">
      <polygon fill="#2b2b2b" points="0,27 205,27 205,0 297,52.5 205,105 205,77 0,77"/>
    </svg>
  </main>
</body>
</html>
```